Boutique custom software development company needs new business card

Our nearly 20 year old custom software development company would like to better include the fact that we are now providing Bitcoin services. These new services are B2B include education (how to acquire and securely hold Bitcoin) and integrating Bitcoin payments into existing ecommerce sites or other existing systems. Please keep the card clean and simple. Attached is our current design and some other files. vextorial.com

Target Market(s)

businesses owners interested in long term relationship

Industry/Entity Type

Custom software development and Bitcoin

Contact Information for Business Card

Dale Parker, dale@vextorial.com, vextorial.com, (888) 555-VXTRL

Font styles to use
Other font styles liked:
• monospace

Requirements
Must have
• double-sided
Nice to have
• clean and simple
Should not have
• physical address

```html
<!DOCTYPE html>
<html lang="en">
<head>
<meta charset="utf-8">
<title>Vextorial business card</title>
<link href="https://fonts.googleapis.com/css2?family=Montserrat:wght@400;600;800&family=Open+Sans:wght@400;600&display=swap" rel="stylesheet">
<style>
  :root {
    --backdrop: #3b3b3b;
    --card: #131313;
    --card-back: #0d0d0d;
    --blue: #3f78c4;
    --orange: #f07a1f;
    --light: #e8e8e8;
  }
  * { box-sizing: border-box; margin: 0; padding: 0; }
  html, body { width: 1200px; height: 801px; overflow: hidden; }
  body {
    background: var(--backdrop);
    font-family: "Open Sans", sans-serif;
    position: relative;
  }
  .card {
    position: absolute;
    top: 252px;
    width: 520px;
    height: 297px;
    border-bottom: 2px solid var(--blue);
    border-left: 1px solid var(--blue);
    overflow: hidden;
  }
  .card-front { left: 40px; background: var(--card); }
  .card-back { left: 640px; background: var(--card-back); }

  .brand { position: absolute; right: 34px; top: 34px; text-align: left; }
  .brand-name {
    font-family: "Montserrat", sans-serif;
    font-weight: 800;
    font-size: 40px;
    letter-spacing: 1px;
    color: var(--blue);
    line-height: 1;
  }
  .brand-tagline {
    font-family: "Open Sans", sans-serif;
    font-size: 12.5px;
    color: var(--blue);
    margin-top: 4px;
  }
  .divider {
    position: absolute;
    left: 30px; right: 40px; top: 178px;
    height: 1px; background: var(--blue);
  }
  .person-name {
    position: absolute; left: 34px; top: 146px;
    font-family: "Montserrat", sans-serif;
    font-weight: 600; font-size: 21px;
    color: var(--blue); letter-spacing: 0.5px;
  }
  .contact-list { position: absolute; left: 34px; top: 192px; list-style: none; }
  .contact-item {
    display: flex; align-items: center; gap: 9px;
    font-family: "Montserrat", sans-serif;
    font-size: 14.5px; color: var(--light);
    line-height: 24px;
  }
  .contact-icon { width: 12px; height: 12px; fill: var(--orange); flex: none; }
  .website {
    position: absolute; right: 40px; top: 190px;
    font-family: "Montserrat", sans-serif;
    font-size: 14px; color: var(--light);
  }
  .website .accent { color: var(--orange); }
  .orange-bar {
    position: absolute; right: 0; top: 218px;
    width: 150px; height: 11px; background: var(--orange);
  }

  .pattern-field {
    position: absolute; inset: 0;
    background: linear-gradient(120deg, #0a0a0a 0%, #1f1f1f 45%, #0c0c0c 70%, #181818 100%);
  }
  .back-brand {
    position: absolute; right: 92px; top: 128px;
    display: flex; align-items: center; gap: 10px;
    background: var(--card-back); padding: 8px 12px;
  }
  .back-square { width: 22px; height: 22px; background: var(--blue); }
  .back-name {
    font-family: "Montserrat", sans-serif;
    font-weight: 800; font-size: 20px; color: var(--blue);
  }
</style>
</head>
<body>
  <section class="card card-front">
    <div class="brand">
      <div class="brand-name">VEXTORIAL</div>
      <div class="brand-tagline">developer of custom applications</div>
    </div>
    <div class="person-name">DALE PARKER</div>
    <div class="divider"></div>
    <ul class="contact-list">
      <li class="contact-item">
        <svg class="contact-icon" viewBox="0 0 24 24"><path d="M6.6 10.8a15.1 15.1 0 0 0 6.6 6.6l2.2-2.2a1 1 0 0 1 1-.25 11.4 11.4 0 0 0 3.6.57 1 1 0 0 1 1 1V20a1 1 0 0 1-1 1A17 17 0 0 1 3 4a1 1 0 0 1 1-1h3.5a1 1 0 0 1 1 1c0 1.25.2 2.45.57 3.57a1 1 0 0 1-.25 1z"/></svg>
        (888) 555-VXTRL
      </li>
      <li class="contact-item">
        <svg class="contact-icon" viewBox="0 0 24 24"><path d="M2 5h20v14H2z M2 5l10 8 10-8" fill="var(--orange)"/><path d="M2 5l10 8 10-8" fill="none" stroke="#131313" stroke-width="2"/></svg>
        dale@vextorial.com
      </li>
    </ul>
    <div class="website">www.<span class="accent">vextorial</span>.com</div>
    <div class="orange-bar"></div>
  </section>

  <section class="card card-back">
    <div class="pattern-field" role="img" aria-label="Glossy black tonal pattern of repeated brand marks"></div>
    <div class="back-brand">
      <span class="back-square"></span>
      <span class="back-name">VEXTORIAL</span>
    </div>
  </section>
</body>
</html>
```